Brightmill Data Works

Our company is about IT hardwares and IT solutions. IT hardware such as PC, RAMS, storage and servers. IT solutions such as project management, BA. We are also selling new technology too.

Target Market(s)

Consumer, Small to Medium Business, Corporate

Requirements
Must have
• The business card must have the following:
• Name:
• Title:
• Contact Number:
• Email address:
• Website:
• Color: Must match the logo color upgrade

```html
<!DOCTYPE html>
<html lang="en">
<head>
<meta charset="utf-8">
<title>Brightmill Data Works – Business Card</title>
<link rel="stylesheet" href="https://fonts.googleapis.com/css2?family=Lato:wght@400;700;900&display=swap">
<style>
  :root {
    --backdrop: #161616;
    --card-white: #ffffff;
    --card-dark: #2b2b2b;
    --accent: #dc9a3c;
    --ink: #454545;
    --muted: #3a3a3a;
    --light-text: #f2f2f2;
  }
  * { margin: 0; padding: 0; box-sizing: border-box; }
  html, body {
    width: 1200px; height: 912px; overflow: hidden;
    background: var(--backdrop);
    font-family: "Lato", sans-serif;
  }
  .canvas { position: relative; width: 1200px; height: 912px; }
  .card {
    position: absolute; width: 620px; height: 354px;
    overflow: hidden; background: var(--card-white);
  }
  .card--front { left: 60px; top: 70px; }
  .card--back { left: 520px; top: 488px; }
  .card__bg { position: absolute; inset: 0; }

  .brand { display: flex; align-items: center; gap: 16px; }
  .brand__dot { width: 30px; height: 30px; border-radius: 50%; background: var(--accent); flex: none; }
  .brand__name {
    font-weight: 900; color: var(--ink); font-size: 34px;
    letter-spacing: 1px; text-transform: uppercase; line-height: 1.05;
  }

  .card--front .brand { position: absolute; left: 0; right: 0; top: 110px; justify-content: center; }
  .card--front .website {
    position: absolute; left: 0; right: 0; top: 232px;
    text-align: center; color: var(--muted); font-size: 17px; letter-spacing: .5px;
  }

  .card--back .brand { position: absolute; left: 44px; top: 100px; }

  .contact {
    position: absolute; right: 24px; top: 92px; text-align: right; color: var(--light-text);
  }
  .contact__name { color: var(--accent); font-weight: 700; font-size: 22px; line-height: 1.2; }
  .contact__title { font-size: 13px; margin-bottom: 14px; }
  .contact__list { list-style: none; font-size: 14px; line-height: 1.7; }
  .contact__list li { display: flex; justify-content: flex-end; align-items: center; gap: 8px; }
  .contact__list svg { width: 13px; height: 13px; fill: var(--accent); flex: none; }

  .address {
    position: absolute; left: 44px; bottom: 20px;
    color: var(--light-text); font-size: 17px; line-height: 1.35;
  }
</style>
</head>
<body>
<main class="canvas">

  <section class="card card--front" aria-label="Card front">
    <div class="brand">
      <span class="brand__dot"></span>
      <span class="brand__name">Brightmill<br>Data Works</span>
    </div>
    <p class="website">www.brightmilldata.com</p>
  </section>

  <section class="card card--back" aria-label="Card back">
    <svg class="card__bg" viewBox="0 0 620 354" preserveAspectRatio="none" aria-hidden="true">
      <rect width="620" height="354" fill="var(--card-dark)"/>
      <path d="M0 0 H380 C410 110 330 250 0 300 Z" fill="var(--card-white)"/>
      <path d="M392 0 C420 100 380 190 300 250" fill="none" stroke="var(--accent)" stroke-width="5"/>
    </svg>

    <div class="brand">
      <span class="brand__dot"></span>
      <span class="brand__name">Brightmill<br>Data Works</span>
    </div>

    <div class="contact">
      <p class="contact__name">Daniel Hartwell</p>
      <p class="contact__title">Manager</p>
      <ul class="contact__list">
        <li>555 014 2200
          <svg viewBox="0 0 16 16"><path d="M3 1l3 0 1 4-2 1a9 9 0 0 0 5 5l1-2 4 1v3a2 2 0 0 1-2 2C7 15 1 9 1 3a2 2 0 0 1 2-2z"/></svg></li>
        <li>555 014 2201
          <svg viewBox="0 0 16 16"><rect x="4" y="1" width="8" height="4"/><rect x="1" y="6" width="14" height="6" rx="1"/><rect x="4" y="10" width="8" height="5"/></svg></li>
        <li>info@brightmilldata.com
          <svg viewBox="0 0 16 16"><path d="M1 3h14v10H1z M2 4l6 5 6-5" stroke="#2b2b2b" stroke-width="1"/></svg></li>
        <li>www.brightmilldata.com
          <svg viewBox="0 0 16 16"><circle cx="8" cy="8" r="7"/><path d="M1 8h14M8 1c-3 4-3 10 0 14M8 1c3 4 3 10 0 14" stroke="#2b2b2b" fill="none"/></svg></li>
      </ul>
    </div>

    <p class="address">48 Alder Row<br>Austin, TX 78701</p>
  </section>

</main>
</body>
</html>
```